FernPath....... a dash of Glow

I need a web design for a new business based in London that will be mobile (offered at homes, parks or a local cafe ect) called FernPath. I offer Life Coaching/Counselling sessions, Personal training, Massage and Sports Massage. Sessions range from an hour to half and hour. My aim is to help people along their journey to help give them gain clarity of where there going, helping them to towards their goals, so that can experience bliss. My website should represent a place people can come to release their stress and worries so that they leave feeling lighter, clearer and happier. I would like my website to reflect someone feeling ALIVE. I would also like a logo design for FernPath with a sentence underneath or near saying a dash of Glow.

Target Market(s)

middle class people

Industry/Entity Type

Business

Coding

Coded - Design and coding required

Number of Pages Required

4 page

Requirements
Must have
• 1st page About us
• 2nd page Services
• 3rd page Prices
• 4th page contact details
Nice to have
• mixture of cultures in images

```html
<!DOCTYPE html>
<html lang="en">
<head>
<meta charset="utf-8">
<title>FernPath – a dash of Glow</title>
<link href="https://fonts.googleapis.com/css2?family=Lato:ital,wght@0,300;0,400;0,700;0,900;1,400&family=PT+Sans:ital,wght@0,400;0,700;1,400&display=swap" rel="stylesheet">
<style>
  :root{
    --ink:#5a5636;
    --olive:#6b6524;
    --pink:#e9607e;
    --orange:#f0a238;
    --grey:#8c8c8c;
    --light:#a9a9a9;
    --dark:#1c1c1c;
    --bar:#4a0d12;
    --lime:#a7ad14;
  }
  *{box-sizing:border-box;margin:0;padding:0}
  html,body{width:762px;height:1200px;overflow:hidden;background:#fff}
  body{position:relative;font-family:"PT Sans",sans-serif;color:var(--grey)}
  .abs{position:absolute}

  .topbar{left:0;top:0;width:762px;height:3px;background:var(--bar)}
  .header{left:0;top:3px;width:762px;height:81px;background:#fff}
  .brand{left:58px;top:20px;width:92px;text-align:center}
  .brand-dot{display:block;width:12px;height:12px;border-radius:50%;background:var(--pink);margin:0 auto 6px}
  .brand-name{font-family:"Lato",sans-serif;font-size:17px;color:var(--olive);line-height:1}
  .brand-tag{font-family:"Lato",sans-serif;font-size:8.5px;color:var(--olive);letter-spacing:.5px;margin-top:3px}
  .nav{left:316px;top:37px;display:flex;gap:0;font-family:"Lato",sans-serif;font-size:8.8px;color:#6a6a6a}
  .nav span{margin-right:29px;position:relative}
  .nav .active{color:var(--pink)}
  .nav .active::after{content:"";position:absolute;left:-2px;right:-2px;top:15px;height:2px;background:var(--pink)}
  .search{left:688px;top:39px}

  .hero{left:0;top:84px;width:762px;height:304px;
    background:radial-gradient(circle at 62% 40%,#fff4c6 0,#f8c86a 14%,#eaa64c 35%,#c7744a 65%,#8f4f42 100%)}
  .hero-title{left:60px;top:187px;font-family:"Lato",sans-serif;font-weight:900;font-size:36px;color:#fff;letter-spacing:.5px}
  .hero-sub{left:63px;top:228px;font-family:"Lato",sans-serif;font-size:10px;color:#fff;letter-spacing:.8px}
  .arrow{stroke:rgba(255,255,255,.8);stroke-width:1.2;fill:none}

  .section-title{left:0;width:762px;text-align:center;font-family:"Lato",sans-serif;font-size:21px;color:var(--ink)}
  .section-lede{left:0;width:762px;text-align:center;font-style:italic;font-size:7.5px;color:var(--grey)}

  .service{width:160px;text-align:center}
  .ring{width:68px;height:68px;margin:0 auto;border-radius:50%;border:1.5px solid transparent;
    background:linear-gradient(#fff,#fff) padding-box,linear-gradient(135deg,var(--pink),var(--orange)) border-box;
    display:flex;align-items:center;justify-content:center}
  .ring i{display:block;width:30px;height:34px;border-radius:14px;background:linear-gradient(180deg,#f6c067,#f19a6c);opacity:.75}
  .service h3{font-family:"Lato",sans-serif;font-weight:400;font-size:10.5px;color:var(--pink);margin-top:8px}
  .service p{font-size:6.8px;line-height:13px;color:var(--grey);margin-top:4px}

  .about{left:0;top:651px;width:762px;height:204px;
    background:linear-gradient(180deg,#8a6a5c 0%,#7e5246 45%,#5e3c36 100%)}
  .about-title{left:0;top:686px;width:762px;text-align:center;font-family:"Lato",sans-serif;font-size:21px;color:#fff}
  .about-copy{left:118px;top:716px;width:526px;text-align:center;font-size:7.3px;line-height:14.8px;color:#f3e9e4}
  .btn{left:337px;top:785px;width:88px;height:22px;background:linear-gradient(180deg,#b7bc1d,#949a0f);
    color:#fff;font-size:8px;text-align:center;line-height:22px}

  .event-text{width:160px;font-family:"Lato",sans-serif}
  .event-text h4{font-weight:400;font-size:10.5px;color:#555}
  .event-text div{font-size:7.5px;color:var(--light);margin-top:8px;display:flex;align-items:center;gap:6px}
  .left .event-text div{justify-content:flex-end}
  .event-text div+div{margin-top:7px}
  .date{width:48px;height:48px;border-radius:50%;border:1.5px solid transparent;
    background:linear-gradient(#fff,#fff) padding-box,linear-gradient(135deg,var(--orange),var(--pink)) border-box;
    text-align:center;font-family:"Lato",sans-serif;color:#444}
  .date b{display:block;font-weight:400;font-size:7.5px;margin-top:11px}
  .date strong{display:block;font-weight:700;font-size:10px;margin-top:2px}

  .center-brand{left:300px;top:990px;width:164px;text-align:center}
  .center-brand .brand-dot{width:16px;height:16px;margin-bottom:8px}
  .center-brand .name{font-family:"Lato",sans-serif;font-size:22px;color:var(--olive);line-height:1}
  .center-brand .tag{font-family:"Lato",sans-serif;font-size:9.5px;color:var(--grey);letter-spacing:1px;margin-top:5px}

  .footer{left:0;top:1129px;width:762px;height:71px;background:var(--dark)}
  .footnav{left:0;top:1153px;width:762px;text-align:center;font-size:8px;color:#ddd}
  .footnav span{margin:0 5px}
  .copy{left:0;top:1170px;width:762px;text-align:center;font-size:7.5px;color:#ddd}
  .social{left:606px;top:1156px;display:flex;gap:4px}
  .social i{display:block;width:15px;height:15px;border-radius:50%;border:1px solid #ddd}
</style>
</head>
<body>
  <div class="abs topbar"></div>
  <header class="abs header"></header>
  <div class="abs brand">
    <span class="brand-dot"></span>
    <div class="brand-name">FernPath</div>
    <div class="brand-tag">a dash of Glow</div>
  </div>
  <nav class="abs nav">
    <span class="active">Home</span><span>About Us</span><span>Services</span><span>Our Aim</span><span>Testimonials</span><span>Contacts</span>
  </nav>
  <svg class="abs search" width="10" height="10" viewBox="0 0 10 10"><circle cx="4" cy="4" r="3" fill="none" stroke="#e9607e" stroke-width="1.4"/><line x1="6.2" y1="6.2" x2="9" y2="9" stroke="#e9607e" stroke-width="1.5"/></svg>

  <div class="abs hero" role="img" aria-label="Woman with arms raised towards a golden sunrise over misty hills"></div>
  <div class="abs hero-title">FERNPATH</div>
  <div class="abs hero-sub">Life Coaching/Counselling sessions</div>
  <svg class="abs" style="left:22px;top:222px" width="16" height="28"><polyline class="arrow" points="14,2 2,14 14,26"/></svg>
  <svg class="abs" style="left:720px;top:222px" width="16" height="28"><polyline class="arrow" points="2,2 14,14 2,26"/></svg>

  <h2 class="abs section-title" style="top:412px">Welcome to FernPath</h2>
  <p class="abs section-lede" style="top:446px">Nemo enim ipsam voluptatem quia voluptas sit aspernatur aut odit aut fugit, sed quia consequuntur</p>
  <svg class="abs" style="left:62px;top:520px" width="12" height="34"><polyline points="11,1 1,17 11,33" fill="none" stroke="#e4e4e4" stroke-width="1"/></svg>
  <svg class="abs" style="left:688px;top:520px" width="12" height="34"><polyline points="1,1 11,17 1,33" fill="none" stroke="#e4e4e4" stroke-width="1"/></svg>

  <div class="abs service" style="left:114px;top:486px">
    <div class="ring"><i role="img" aria-label="Life coaching icon"></i></div>
    <h3>Life Coaching</h3>
    <p>Nemo enim ipsam voluptatem quia sit aspernatur aut odit aut fugit, sed quia magni dolores eos qui ratione voluptatem</p>
  </div>
  <div class="abs service" style="left:301px;top:486px">
    <div class="ring"><i role="img" aria-label="Personal training icon"></i></div>
    <h3>Personal training</h3>
    <p>Nemo enim ipsam voluptatem quia sit aspernatur aut odit aut fugit, sed quia magni dolores eos qui ratione voluptatem</p>
  </div>
  <div class="abs service" style="left:496px;top:486px">
    <div class="ring"><i role="img" aria-label="Massage stones icon"></i></div>
    <h3>Massage and Sports Massage</h3>
    <p>Nemo enim ipsam voluptatem quia sit aspernatur aut odit aut fugit, sed quia magni dolores eos ...</p>
  </div>

  <section class="abs about" role="img" aria-label="Hiker with backpack looking over hills at dusk"></section>
  <h2 class="abs about-title">About Us</h2>
  <p class="abs about-copy">ut perspiciatis unde omnis iste natus error sit voluptatem accusantium doloremque laudantium, totam rem aperiam, eaque ipsa quae ab illo inventore veritatis et quasi architecto beatae vitae dicconsequuntur magni dolores eos qui ratioula dolor sit amet, consectetam quaerat voluptatem. Ut enim ad minima veniam, quis nostrum exercitationem ullam corporis suscipit laboriosam, nisi ut aliquid ex ea commodi consequatur? Quis autem vel eum iure reprehenderit qui in ea voluptate velit esse quam nihil molestiae consequatur, vel illum qui dolorem eum</p>
  <div class="abs btn">Read More</div>

  <h2 class="abs section-title" style="top:878px">Upcoming Events</h2>
  <p class="abs section-lede" style="top:912px">Nemo enim ipsam voluptatem quia voluptas sit aspernatur aut odit aut fugit, sed quia consequuntur</p>

  <!-- left events -->
  <div class="abs left" style="left:58px;top:965px">
    <div class="event-text" style="text-align:right">
      <h4>Life Coaching/Counselling</h4>
      <div>8.00 am - 5.00 <svg width="8" height="8"><circle cx="4" cy="4" r="3.2" fill="none" stroke="#e9607e"/><polyline points="4,2 4,4 5.5,4" fill="none" stroke="#e9607e"/></svg></div>
      <div>Street Name, City Name <svg width="8" height="9"><path d="M4 9 C1 5 1 4 1 3.5 A3 3 0 0 1 7 3.5 C7 4 7 5 4 9Z" fill="#e9607e"/><circle cx="4" cy="3.5" r="1" fill="#fff"/></svg></div>
    </div>
  </div>
  <div class="abs date" style="left:238px;top:963px"><b>02</b><strong>DEC</strong></div>
  <div class="abs left" style="left:58px;top:1053px">
    <div class="event-text" style="text-align:right">
      <h4>Life Coaching/Counselling</h4>
      <div>8.00 am - 5.00 <svg width="8" height="8"><circle cx="4" cy="4" r="3.2" fill="none" stroke="#e9607e"/><polyline points="4,2 4,4 5.5,4" fill="none" stroke="#e9607e"/></svg></div>
      <div>Street Name, City Name <svg width="8" height="9"><path d="M4 9 C1 5 1 4 1 3.5 A3 3 0 0 1 7 3.5 C7 4 7 5 4 9Z" fill="#e9607e"/><circle cx="4" cy="3.5" r="1" fill="#fff"/></svg></div>
    </div>
  </div>
  <div class="abs date" style="left:238px;top:1051px"><b>02</b><strong>DEC</strong></div>

  <div class="abs center-brand">
    <span class="brand-dot"></span>
    <div class="name">FernPath</div>
    <div class="tag">a dash of Glow</div>
  </div>

  <!-- right events -->
  <div class="abs date" style="left:476px;top:963px"><b>02</b><strong>DEC</strong></div>
  <div class="abs" style="left:541px;top:965px">
    <div class="event-text" style="width:180px">
      <h4>Life Coaching/Counselling</h4>
      <div><svg width="8" height="8"><circle cx="4" cy="4" r="3.2" fill="none" stroke="#e9607e"/><polyline points="4,2 4,4 5.5,4" fill="none" stroke="#e9607e"/></svg> December 02 @ 8.00 am - 5.00</div>
      <div><svg width="8" height="9"><path d="M4 9 C1 5 1 4 1 3.5 A3 3 0 0 1 7 3.5 C7 4 7 5 4 9Z" fill="#e9607e"/><circle cx="4" cy="3.5" r="1" fill="#fff"/></svg> Street Name, City Name</div>
    </div>
  </div>
  <div class="abs date" style="left:476px;top:1051px"><b>02</b><strong>DEC</strong></div>
  <div class="abs" style="left:541px;top:1053px">
    <div class="event-text" style="width:180px">
      <h4>Life Coaching/Counselling</h4>
      <div><svg width="8" height="8"><circle cx="4" cy="4" r="3.2" fill="none" stroke="#e9607e"/><polyline points="4,2 4,4 5.5,4" fill="none" stroke="#e9607e"/></svg> December 02 @ 8.00 am - 5.00</div>
      <div><svg width="8" height="9"><path d="M4 9 C1 5 1 4 1 3.5 A3 3 0 0 1 7 3.5 C7 4 7 5 4 9Z" fill="#e9607e"/><circle cx="4" cy="3.5" r="1" fill="#fff"/></svg> Street Name, City Name</div>
    </div>
  </div>

  <footer class="abs footer"></footer>
  <div class="abs footnav"><span>Home</span>|<span>About Us</span>|<span>Services</span>|<span>Our Aim</span>|<span>Testimonials</span>|<span>Contacts</span></div>
  <div class="abs copy">© 2015. FernPath.com All rights reserved</div>
  <div class="abs social"><i></i><i></i><i></i><i></i><i></i></div>
</body>
</html>
```